Looking for a modern, Professional business card design

We have a simple business card, but are looking for a more modern, professional look. A sample of the basic card is attached as well as the logo. We would also like to add that we offer:
Struggling with your finances?
- Learn to become debt free
- Discover the power of cash
- Control your money instead of it controlling you
Let us help you achieve a new level of financial freedom!
Also, we would like to have a "SPECIAL OFFER!: FREE 30 minute consultation"
Financial Planning

```html
<!DOCTYPE html>
<html lang="en">
<head>
<meta charset="utf-8">
<title>Harbor Money Coaching – Business Card</title>
<link rel="stylesheet" href="https://fonts.googleapis.com/css2?family=Open+Sans:wght@400;600;700&display=swap">
<style>
  :root {
    --backdrop: #e9e7e3;
    --card: #ffffff;
    --ink: #1b1b1b;
    --brand-green: #3c8f2e;
    --tick-green: #6cb33f;
    --rule: #2a2a2a;
  }
  html, body {
    margin: 0;
    width: 1200px;
    height: 1000px;
    overflow: hidden;
    background: var(--backdrop);
    font-family: "Open Sans", Arial, sans-serif;
    color: var(--ink);
  }
  .canvas { position: relative; width: 1200px; height: 1000px; }
  .card {
    position: absolute;
    left: 265px;
    width: 665px;
    height: 397px;
    background: var(--card);
    box-shadow: 0 3px 8px rgba(0,0,0,.25);
  }
  .card--front { top: 73px; }
  .card--back { top: 533px; }

  .brand {
    position: absolute;
    display: flex;
    align-items: center;
    gap: 12px;
    font-weight: 700;
    font-size: 27px;
    color: var(--ink);
    letter-spacing: .2px;
    white-space: nowrap;
  }
  .brand__dot {
    width: 30px; height: 30px; border-radius: 50%;
    background: var(--tick-green);
  }
  .card--front .brand { right: 32px; top: 78px; }
  .card--back .brand { left: 32px; top: 85px; }

  .person { position: absolute; left: 33px; top: 190px; }
  .person__name { margin: 0; font-size: 24px; font-weight: 700; color: var(--brand-green); line-height: 1.2; }
  .person__role { margin: 2px 0 0; font-size: 16px; }

  .contact {
    position: absolute; right: 32px; top: 188px;
    margin: 0; padding: 0; list-style: none;
    text-align: right; font-size: 16px; line-height: 23px;
  }
  .contact li { display: flex; justify-content: flex-end; align-items: center; gap: 7px; }
  .contact svg { width: 14px; height: 14px; fill: var(--brand-green); }
  .contact__address { margin-top: 4px; padding-right: 0; }

  .divider {
    position: absolute; left: 370px; right: 32px; top: 316px;
    border-top: 1.5px solid var(--rule);
  }
  .offer { position: absolute; right: 32px; top: 327px; text-align: right; font-size: 16px; line-height: 22px; }
  .offer__title { font-weight: 700; margin: 0; font-size: 15px; }
  .offer__text { margin: 0; }

  .pitch { position: absolute; left: 343px; top: 198px; width: 300px; font-size: 16px; line-height: 20px; }
  .pitch__question { margin: 0 0 10px; font-weight: 700; }
  .pitch__list { list-style: none; margin: 0; padding: 0; }
  .pitch__list li { position: relative; padding-left: 18px; margin-bottom: 6px; }
  .pitch__list svg { position: absolute; left: -2px; top: 3px; width: 16px; height: 14px; }
  .pitch__close { margin: 4px 0 0; }
</style>
</head>
<body>
<main class="canvas">
  <section class="card card--front">
    <div class="brand"><span class="brand__dot"></span>Harbor Money Coaching</div>

    <div class="person">
      <h1 class="person__name">Daniel Whitford</h1>
      <p class="person__role">Managing Director</p>
    </div>

    <ul class="contact">
      <li>+ 000 000 0000
        <svg viewBox="0 0 14 14"><rect x="3.5" y="0.5" width="7" height="13" rx="1.2"/><rect x="4.8" y="2" width="4.4" height="7" fill="#fff"/></svg></li>
      <li>+ 000 000 0000
        <svg viewBox="0 0 14 14"><path d="M1 5c0-2 3-3 6-3s6 1 6 3v1h-3V4.5H4V6H1z"/><rect x="2.5" y="7" width="9" height="6" rx="1"/></svg></li>
      <li>info@harbormoneycoach.com
        <svg viewBox="0 0 14 14"><rect x="0.5" y="2.5" width="13" height="9"/><path d="M1 3l6 5 6-5" stroke="#fff" stroke-width="1.2" fill="none"/></svg></li>
      <li>www.harbormoneycoach.com
        <svg viewBox="0 0 14 14"><circle cx="7" cy="7" r="6.5"/><path d="M.5 7h13M7 .5c-3 3-3 10 0 13M7 .5c3 3 3 10 0 13" stroke="#fff" stroke-width="1" fill="none"/></svg></li>
      <li class="contact__address">48 Linden Row, Millbrook, NY 1250</li>
    </ul>

    <div class="divider"></div>

    <div class="offer">
      <p class="offer__title">SPECIAL OFFER!:</p>
      <p class="offer__text">FREE 30 minute consultation</p>
    </div>
  </section>

  <section class="card card--back">
    <div class="brand"><span class="brand__dot"></span>Harbor Money Coaching</div>

    <div class="pitch">
      <p class="pitch__question">Struggling with your finances?</p>
      <ul class="pitch__list">
        <li><svg viewBox="0 0 16 14"><path d="M1 7l4 5L15 1" stroke="var(--tick-green)" stroke-width="2.4" fill="none" stroke-linecap="round"/></svg>Learn to become debt free</li>
        <li><svg viewBox="0 0 16 14"><path d="M1 7l4 5L15 1" stroke="var(--tick-green)" stroke-width="2.4" fill="none" stroke-linecap="round"/></svg>Discover the power of cash</li>
        <li><svg viewBox="0 0 16 14"><path d="M1 7l4 5L15 1" stroke="var(--tick-green)" stroke-width="2.4" fill="none" stroke-linecap="round"/></svg>Control your money instead of it controlling you</li>
      </ul>
      <p class="pitch__close">Let us help you achieve a new level of financial freedom!</p>
    </div>
  </section>
</main>
</body>
</html>
```